Granite Bureau of Analysis Card Design

I need a business card for the agency I currently am tasked with, which is based in Hartford, CT. GBAN provides, disseminates and obtains intelligence in regards to ongoing criminal investigations throughout the State of CT. The information we obtain and provide, comes to us and is sent out by various Law Enforcement agencies throughout CT.

Industry/Entity Type

Business

Contact Information for Business Card

Officer Lyle P. Harrowby
Bramford Police Department - Eastern Region Intelligence Officer
Granite Bureau of Analysis
4827 Willowmere Ave., Middletown, CT 06457
Work Cell: (555) 318-2694
E-Mail: gban.wd@gbanmail.example

```html
<!DOCTYPE html>
<html lang="en">
<head>
<meta charset="utf-8">
<title>Granite Bureau of Analysis – Business Card</title>
<link rel="stylesheet" href="https://fonts.googleapis.com/css2?family=Michroma&display=swap">
<style>
  :root {
    --backdrop: #e6e6e6;
    --card: #ffffff;
    --ink: #3a3a3a;
    --accent-red: #b72a25;
    --accent-gold: #e0c53c;
    --rule: #9a9a9a;
    --patch-dark: #1b1b1b;
  }
  * { box-sizing: border-box; margin: 0; padding: 0; }
  html, body {
    width: 1200px; height: 900px; overflow: hidden;
    background: var(--backdrop);
    font-family: "Michroma", sans-serif;
  }
  .card {
    position: absolute; left: 100px; top: 164px;
    width: 1000px; height: 572px;
    background: var(--card);
    box-shadow: 0 10px 30px rgba(0,0,0,.18);
    overflow: hidden;
  }
  .card__band { position: absolute; inset: 0; width: 100%; height: 100%; }
  .agency-mark {
    position: absolute; left: 320px; top: 84px;
    display: flex; align-items: center; gap: 14px;
  }
  .agency-mark__square { width: 34px; height: 34px; background: var(--patch-dark); }
  .agency-mark__name {
    font-size: 19px; color: var(--patch-dark); letter-spacing: 1px;
    font-variant: small-caps;
  }
  .identity {
    position: absolute; right: 520px; top: 212px;
    text-align: right; color: var(--ink);
    font-variant: small-caps; letter-spacing: 1.5px;
  }
  .identity__name { color: var(--accent-red); font-size: 19px; }
  .identity__title { font-size: 13px; margin-top: 8px; line-height: 1.6; }
  .identity__address { font-size: 13px; margin-top: 20px; line-height: 1.75; }
  .divider {
    position: absolute; left: 500px; top: 205px;
    width: 1px; height: 170px; background: var(--rule);
  }
  .contacts {
    position: absolute; left: 522px; top: 228px;
    list-style: none; color: var(--ink);
    font-size: 14px; letter-spacing: 1.5px; font-variant: small-caps;
  }
  .contacts li { display: flex; align-items: center; gap: 10px; height: 30px; }
  .contacts li.contacts__gap { margin-top: 14px; }
  .contacts svg { width: 16px; height: 16px; flex: none; }
  .band-name {
    position: absolute; right: 90px; bottom: 40px;
    color: #fff; font-size: 15px; letter-spacing: 3px; font-variant: small-caps;
    transform: rotate(-6deg);
  }
</style>
</head>
<body>
<main class="card">
  <svg class="card__band" viewBox="0 0 1000 572" preserveAspectRatio="none" aria-hidden="true">
    <path d="M0 572 C 300 530 700 460 1000 392 L1000 572 Z" fill="var(--accent-gold)"/>
    <path d="M0 572 C 300 538 700 472 1000 404 L1000 572 Z" fill="var(--accent-red)"/>
  </svg>

  <div class="agency-mark">
    <span class="agency-mark__square"></span>
    <span class="agency-mark__name">Bramford Police</span>
  </div>

  <section class="identity">
    <p class="identity__name">Officer Lyle P. Harrowby</p>
    <p class="identity__title">Bramford Police Department<br>Eastern Region Intelligence Officer</p>
    <p class="identity__address">4827 Willowmere Ave.,<br>Middletown, CT 06457</p>
  </section>

  <div class="divider"></div>

  <ul class="contacts">
    <li><svg viewBox="0 0 16 16"><circle cx="8" cy="8" r="8" fill="var(--accent-red)"/><rect x="5.5" y="3.5" width="5" height="9" rx="1" fill="#fff"/></svg>Work Cell: (555) 318-2694</li>
    <li class="contacts__gap"><svg viewBox="0 0 16 16"><circle cx="8" cy="8" r="8" fill="var(--accent-red)"/><rect x="4" y="5" width="8" height="6" fill="#fff"/><path d="M4 5l4 3 4-3" stroke="var(--accent-red)" fill="none"/></svg>gban.wd@gbanmail.example</li>
    <li><svg viewBox="0 0 16 16"><circle cx="8" cy="8" r="8" fill="var(--accent-red)"/><rect x="4" y="6" width="8" height="5" fill="#fff"/><rect x="5.5" y="4" width="5" height="2" fill="#fff"/></svg>Granite Bureau of Analysis</li>
  </ul>

  <p class="band-name">Granite Bureau of Analysis</p>
</main>
</body>
</html>
```